VIP Card Design Project

uZorvo is a premium sneaker store selling brand name sneakers like Volta, Rexa, Kembro and etc. ( www.uzorvoshop.com ) We need to design a VIP card to promote one of our discount program called "Uzorvo VIP Band 17", which offers 24% discount off all full-priced items. The idea is because we have a "Peakline Gym center" (peaklinegym.com) next door and we are trying to design a discount program for people going to the fitness center.
The design is for the front of the card. The back will be black and white with benefits information and member information.
The front design need to include our logo, "VIP", "Band 17" and our web address "Uzorvo.com" and Chatterly and quibbr logo.
It will be a plastic card in the size of 3.375x2.125 (bleed size 3.5x2.25)

```html
<!DOCTYPE html>
<html lang="en">
<head>
<meta charset="utf-8">
<title>Uzorvo VIP Band 17 Card</title>
<link rel="stylesheet" href="https://fonts.googleapis.com/css2?family=Merriweather:wght@700;900&family=Arimo:wght@400;700&display=swap">
<style>
  :root {
    --bg: #ece7e1;
    --card-white: #ffffff;
    --brand-orange: #f39a1f;
    --green-dark: #1f5a1c;
    --green-light: #8cc63f;
    --panel-black: #111111;
    --panel-grey: #3b3b3b;
    --accent-red: #e31e24;
    --text-white: #ffffff;
    --photo-silver: #b9bcbf;
    --photo-blue: #5b9bd5;
    --photo-dark: #2d3436;
    --social-blue: #3b5b98;
    --social-sky: #35a8dd;
  }
  * { margin: 0; padding: 0; box-sizing: border-box; }
  html, body { width: 1200px; height: 435px; overflow: hidden; background: var(--bg); }
  .stage { position: relative; width: 1200px; height: 435px; }

  .card { position: absolute; width: 512px; height: 320px; box-shadow: 2px 3px 6px rgba(0,0,0,.35); }
  .card--front { left: 55px; top: 58px; background: var(--card-white); }
  .card--back {
    left: 645px; top: 58px; width: 507px; height: 318px;
    background: linear-gradient(90deg, #000 0%, #0d0303 45%, #5a0a0d 72%, var(--accent-red) 100%);
    font-family: "Arimo", Arial, sans-serif; color: var(--text-white);
  }

  .tile { position: absolute; }
  .photo { position: absolute; }
  .photo--silver { left: 0; top: 0; width: 150px; height: 100px;
    background: linear-gradient(160deg, #7d8a86 0%, var(--photo-silver) 45%, #6f7b78 100%); }
  .photo--blue { left: 356px; top: 110px; width: 156px; height: 100px;
    background: linear-gradient(160deg, #d9dde0 0%, var(--photo-blue) 55%, #c7ccd0 100%); }
  .photo--dark { left: 0; top: 220px; width: 150px; height: 100px;
    background: linear-gradient(160deg, #6e7a77 0%, var(--photo-dark) 50%, #b7d33a 85%, #7c8885 100%); }

  .brand { font-family: "Merriweather", Georgia, serif; font-weight: 900; color: var(--brand-orange); letter-spacing: 1px; }

  .tile--headline { left: 160px; top: 0; width: 352px; height: 100px;
    background: linear-gradient(90deg, var(--green-dark) 0%, #3e8a2a 50%, var(--green-light) 100%); }
  .tile--headline .brand { position: absolute; left: 12px; top: 4px; font-size: 40px; }
  .tagline { position: absolute; left: 12px; top: 66px; font-family: "Merriweather", Georgia, serif;
    font-weight: 700; font-size: 16px; color: var(--text-white); }

  .tile--club { left: 0; top: 110px; width: 348px; height: 100px;
    background: linear-gradient(90deg, var(--panel-grey) 0%, #1f1f1f 55%, var(--panel-black) 100%); }
  .tile--club .brand { position: absolute; left: 12px; top: 2px; font-size: 36px; opacity: .4; }
  .club-name { position: absolute; left: 10px; top: 58px; font-family: "Merriweather", Georgia, serif;
    font-weight: 700; font-size: 19px; color: var(--text-white); }
  .discount-burst { position: absolute; left: 232px; top: 2px; width: 114px; height: 96px; }

  .tile--contact { left: 160px; top: 220px; width: 352px; height: 100px;
    background: linear-gradient(90deg, var(--panel-black) 0%, #2a0507 45%, #8a1114 75%, var(--accent-red) 100%); }
  .social { position: absolute; top: 16px; display: flex; align-items: center; gap: 5px;
    font-family: "Merriweather", Georgia, serif; font-weight: 700; font-size: 10px; color: var(--text-white); }
  .social--chat { left: 14px; }
  .social--quib { left: 104px; }
  .social-mark { width: 24px; height: 24px; border-radius: 4px; }
  .social--chat .social-mark { background: var(--social-blue); }
  .social--quib .social-mark { background: var(--social-sky); }
  .web { position: absolute; left: 12px; top: 70px; font-family: "Merriweather", Georgia, serif;
    font-weight: 700; font-size: 14px; letter-spacing: 1.5px; color: var(--text-white); }
  .tile--contact .brand { position: absolute; left: 192px; top: 50px; font-size: 34px; opacity: .75; }

  .member-line { position: absolute; left: 40px; top: 32px; font-size: 10px; }
  .benefits-title { position: absolute; left: 40px; top: 62px; font-size: 17px; font-weight: 700; color: var(--accent-red); }
  .benefits-intro { position: absolute; left: 40px; top: 86px; font-size: 11px; }
  .benefits-list { position: absolute; left: 40px; top: 122px; width: 450px; list-style: none; font-size: 11px; line-height: 16px; }
  .benefits-list li { position: relative; padding-left: 13px; margin-bottom: 5px; }
  .benefits-list .marker { position: absolute; left: 0; color: var(--accent-red); }
</style>
</head>
<body>
<main class="stage">

  <section class="card card--front" aria-label="Card front">
    <div class="photo photo--silver" role="img" aria-label="Photo of a silver and red running shoe"></div>
    <div class="tile tile--headline">
      <span class="brand">uZorvo</span>
      <p class="tagline">discount off all full-priced items.</p>
    </div>

    <div class="tile tile--club">
      <span class="brand">uZorvo</span>
      <p class="club-name">Uzorvo VIP Band 17</p>
      <svg class="discount-burst" viewBox="0 0 114 96" aria-label="24% off">
        <polygon fill="#ffffff" points="57,2 64,14 76,6 78,20 92,16 88,30 104,30 96,42 110,48 96,54 104,66 88,66 92,80 78,76 76,90 64,82 57,94 50,82 38,90 36,76 22,80 26,66 10,66 18,54 4,48 18,42 10,30 26,30 22,16 36,20 38,6 50,14"/>
        <text x="57" y="60" text-anchor="middle" transform="rotate(-22 57 48)" font-family="Merriweather, Georgia, serif" font-weight="900" font-size="32" fill="#e31e24">24%</text>
      </svg>
    </div>
    <div class="photo photo--blue" role="img" aria-label="Photo of a blue and white running shoe"></div>

    <div class="photo photo--dark" role="img" aria-label="Photo of a black running shoe with lime sole"></div>
    <div class="tile tile--contact">
      <div class="social social--chat"><span class="social-mark"></span>Chatterly</div>
      <div class="social social--quib"><span class="social-mark"></span>quibbr</div>
      <p class="web">www.Uzorvo.com</p>
      <span class="brand">uZorvo</span>
    </div>
  </section>

  <section class="card card--back" aria-label="Card back">
    <p class="member-line">Member Name :..........................................................Member ID :..........................................................</p>
    <h2 class="benefits-title">Benefits :-</h2>
    <p class="benefits-intro">The UZORVO Member Program entitles Members to the following benefits:</p>
    <ol class="benefits-list">
      <li><span class="marker">a.</span>20% OFF your entire first purchase after you sign up (Limited Time Offer).<br>Certain items are excluded from this offer. Please see stores for details.</li>
      <li><span class="marker">b.</span>10% OFF every purchase while being a member.<br>Certain items are excluded from this offer. Please see stores for details.</li>
      <li><span class="marker">c.</span>Additional 10% OFF and FREE SHIPPING when an item is out of stock<br>in store but can be shipped to you from another location.</li>
      <li><span class="marker">d.</span>Eligible to purchase exclusive items offered to members only.<br>Purchasing of exclusive items is limited to 1 item per member per 30 days.<br>Please see stores for details.</li>
    </ol>
  </section>

</main>
</body>
</html>
```